Website for 3d printing & other services

Hi, i'm after a website to sell my 3d printed automotive parts as well as sell my 3d printing services & other services.

There's a few things i need the website to have:

- Automatic 3d print quoting based on the file the client uploads to the website.
- Shop function where i can sell my custom automotive parts
- 3D printing technologies offered are SLA & FDM
- My business can offer 3d printing, 3d scanning, 3d cad design, cnc machining, steel fabrication, drafting services.

The color design is to suit my logo which is Black, orange & white.

Target Market(s)

3d printing, automotive, fabrication

Industry/Entity Type

General manufacturing & Custom automotive parts

Coding

Coded - Design and coding required

Number of Pages Required

5+ page

Requirements
Must have
• Automatic 3d print quoting. Shop for my printed parts.

```html
<!DOCTYPE html>
<html lang="en">
<head>
<meta charset="utf-8">
<title>Kestrel Draft &amp; Design</title>
<link href="https://fonts.googleapis.com/css2?family=Krona+One&family=Roboto:wght@400;500;700&display=swap" rel="stylesheet">
<style>
:root{
  --orange:#f97316;
  --orange-deep:#ef6a0c;
  --black:#0b0b0b;
  --white:#ffffff;
  --text:#555555;
  --heading:#111111;
  --field:#edf0f6;
  --line:#e6e6e6;
}
*{box-sizing:border-box;margin:0;padding:0}
html,body{width:1200px;height:5021px;overflow:hidden}
body{position:relative;background:var(--white);font-family:"Roboto",Arial,sans-serif;color:var(--text)}
.abs{position:absolute}
.display{font-family:"Krona One","Arial Black",sans-serif;color:var(--heading);text-transform:uppercase;letter-spacing:1px}
.btn{position:absolute;display:flex;align-items:center;justify-content:center;background:var(--orange);color:var(--white);font-size:14px;font-weight:500;border-radius:2px}
.rule{position:absolute;left:540px;width:120px;height:3px;background:var(--orange)}
/* header */
.topline{position:absolute;left:0;top:0;width:1200px;height:5px;background:var(--orange)}
.brand-box{position:absolute;left:111px;top:0;width:207px;height:185px;background:var(--black);display:flex;flex-direction:column;align-items:center;justify-content:center;gap:12px}
.brand-box .sq{width:34px;height:34px;background:var(--orange)}
.brand-name{font-weight:700;color:var(--orange);font-size:17px;text-align:center;line-height:1.25}
.btn-phone{background:var(--black)}
.nav{position:absolute;top:112px;left:410px;display:flex;gap:0;font-size:14px;font-weight:500;color:#222}
.nav span{position:absolute;white-space:nowrap}
/* hero */
.hero{position:absolute;left:0;top:185px;width:1200px;height:581px;background:linear-gradient(100deg,#2f8fd3 0%,#3ea0e0 40%,#6fb9e6 70%,#d9dfe4 100%)}
.hero-title{position:absolute;left:111px;color:var(--white);font-family:"Krona One","Arial Black",sans-serif}
.hero p{position:absolute;left:111px;top:492px;width:500px;color:var(--white);font-size:15px;line-height:29px}
/* offer */
.lead{position:absolute;text-align:center;font-size:14.5px;line-height:32px;color:#666}
.card{position:absolute;top:1114px;width:236px;height:314px;background:var(--white);box-shadow:0 2px 10px rgba(0,0,0,.10)}
.card .ph{position:absolute;left:6px;top:6px;width:224px;height:250px}
.card .lbl{position:absolute;left:0;right:0;top:278px;text-align:center;font-size:15px;font-weight:500;color:#222}
.arrow{position:absolute;top:1467px;width:35px;height:35px;border-radius:50%;display:flex;align-items:center;justify-content:center}
/* tech */
.tech-h{position:absolute;font-family:"Krona One","Arial Black",sans-serif;font-size:30px;color:var(--heading)}
.tech-p{position:absolute;width:450px;font-size:14.5px;line-height:32px;color:#666}
.tech-img{position:absolute;border-radius:6px}
/* shop */
.shop{position:absolute;left:0;top:3043px;width:1200px;height:705px;background:linear-gradient(180deg,#f7781a,#f36f10)}
.prod{position:absolute;top:239px;width:230px;height:275px;background:var(--white);border-radius:3px}
.prod .ph{position:absolute;left:25px;top:25px;width:180px;height:180px;border-radius:4px}
.prod-meta{position:absolute;top:535px;width:230px;text-align:center;color:var(--white)}
.stars{font-size:10px;letter-spacing:1px}
.pname{font-size:15.5px;font-weight:700;margin-top:12px}
.price{font-size:19px;font-weight:700;margin-top:10px}
/* form */
.flabel{position:absolute;font-size:13px;color:#222}
.field{position:absolute;height:52px;background:var(--field);font-size:12.5px;color:#777;display:flex;align-items:center;justify-content:space-between;padding:0 30px 0 35px}
/* footer */
.footer{position:absolute;left:0;top:4660px;width:1200px;height:361px;background:var(--black);color:var(--white)}
.fh{position:absolute;top:80px;font-family:"Krona One","Arial Black",sans-serif;font-size:17px;letter-spacing:1px}
.fl{position:absolute;font-size:14.5px;line-height:33px}
</style>
</head>
<body>
<div class="topline"></div>
<div class="brand-box"><div class="sq"></div><div class="brand-name">Kestrel<br>Draft &amp; Design</div></div>
<div class="btn" style="left:768px;top:43px;width:144px;height:43px">Get Started</div>
<div class="btn btn-phone" style="left:933px;top:43px;width:154px;height:43px">+1 555 014 2290</div>
<svg class="abs" style="left:407px;top:114px" width="16" height="14" viewBox="0 0 16 14"><path d="M8 0 0 7h2v7h4V9h4v5h4V7h2z" fill="#f97316"/></svg>
<div class="abs" style="top:114px;left:446px;font-size:14px;font-weight:500;color:#222">About Us</div>
<div class="abs" style="top:114px;left:551px;font-size:14px;font-weight:500;color:#222">Services</div>
<div class="abs" style="top:114px;left:652px;font-size:14px;font-weight:500;color:#222">Custom Automotive Parts</div>
<div class="abs" style="top:114px;left:873px;font-size:14px;font-weight:500;color:#222">3D Printing Technologies</div>
<svg class="abs" style="left:1073px;top:114px" width="16" height="14" viewBox="0 0 16 14"><path d="M0 1h3l2 8h9l2-6H4" stroke="#f97316" stroke-width="2" fill="none"/><circle cx="6" cy="12" r="1.6" fill="#f97316"/><circle cx="13" cy="12" r="1.6" fill="#f97316"/></svg>

<section class="hero" role="img" aria-label="3D printer nozzle printing a yellow part on a blue-lit print bed">
  <div class="hero-title" style="top:117px;font-size:33px">WELCOME TO</div>
  <div class="hero-title" style="top:167px;font-size:50px;line-height:66px">KESTREL DRAFT &amp;<br>DESIGN</div>
  <p>I must explain to you how all this mistaken idea of denouncing pleasure and praising pain was born and I will give you a complete account of the system, and expound the actual teachings</p>
  <div class="btn" style="left:111px;top:417px;width:144px;height:37px">Get Started</div>
</section>

<h2 class="display abs" style="top:872px;left:0;width:1200px;text-align:center;font-size:36px">What We Offer</h2>
<div class="rule" style="top:924px"></div>
<p class="lead" style="left:135px;top:972px;width:930px">I must explain to you how all this mistaken idea of denouncing pleasure and praising pain was born and I will give you a complete account of the system, and expound the actual teachings of the great explorer of the truth, the master-builder of human happiness. No one rejects, dislikes</p>
<div class="card" style="left:107px"><div class="ph" role="img" aria-label="3D printer printing a red lattice part" style="background:linear-gradient(180deg,#3a8fd0,#1d5c9c 60%,#c8322a)"></div><div class="lbl">3D Printing</div></div>
<div class="card" style="left:357px"><div class="ph" role="img" aria-label="3D scanning room with scanner equipment" style="background:linear-gradient(180deg,#dfe6ec,#b9c6d1)"></div><div class="lbl">3D Scanning</div></div>
<div class="card" style="left:607px"><div class="ph" role="img" aria-label="CAD model of an engine on a monitor" style="background:linear-gradient(180deg,#4f86b8,#1f3c5e)"></div><div class="lbl">3D Cad Design</div></div>
<div class="card" style="left:857px"><div class="ph" role="img" aria-label="Sparks from steel cutting" style="background:linear-gradient(135deg,#3a2a22,#c9702f 55%,#6a5a52)"></div><div class="lbl">Steel Fabrication</div></div>
<div class="arrow" style="left:560px;background:#fff;box-shadow:0 1px 5px rgba(0,0,0,.15)"><svg width="10" height="10" viewBox="0 0 10 10"><path d="M7 1 3 5l4 4" stroke="#222" stroke-width="2" fill="none"/></svg></div>
<div class="arrow" style="left:604px;background:var(--orange)"><svg width="10" height="10" viewBox="0 0 10 10"><path d="M3 1l4 4-4 4" stroke="#fff" stroke-width="2" fill="none"/></svg></div>

<h2 class="display abs" style="top:1596px;left:0;width:1200px;text-align:center;font-size:36px">3D Printing Technologies</h2>
<div class="rule" style="top:1657px"></div>
<p class="lead" style="left:150px;top:1689px;width:900px">I must explain to you how all this mistaken idea of denouncing pleasure and praising pain was born and I will give you a complete account of the system, and expound the actual teachings of the great explorer of the truth, the master-builder of human</p>

<div class="tech-h" style="left:111px;top:1825px">SLA</div>
<p class="tech-p" style="left:111px;top:1879px">I must explain to you how all this mistaken idea of denouncing pleasure and praising pain was born and I will give you a complete account of the system, and expound the actual teachings of the great explorer of the truth, the master-builder of human happiness. No one rejects, dislikes, or avoids pleasure itself, because it is pleasure</p>
<p class="tech-p" style="left:111px;top:2101px">Nor again is there anyone who loves or pursues or desires to obtain pain of itself, because it is pain, but because occasionally circumstances occur in which toil</p>
<div class="btn" style="left:111px;top:2226px;width:111px;height:42px">Read More</div>
<div class="tech-img" role="img" aria-label="Hands adjusting a desktop 3D printer" style="left:617px;top:1802px;width:470px;height:497px;background:linear-gradient(135deg,#2b2b2b,#6b625a 45%,#e9c8a2 75%,#3a3a3a)"></div>

<div class="tech-img" role="img" aria-label="FDM printer nozzle extruding a Y-shaped part, blue tone" style="left:111px;top:2398px;width:471px;height:497px;background:linear-gradient(160deg,#9fb9cf,#3f6383 55%,#1c2f44)"></div>
<div class="tech-h" style="left:635px;top:2423px">FDM</div>
<p class="tech-p" style="left:635px;top:2477px">I must explain to you how all this mistaken idea of denouncing pleasure and praising pain was born and I will give you a complete account of the system, and expound the actual teachings of the great explorer of the truth, the master-builder of human happiness. No one rejects, dislikes, or avoids pleasure itself, because it is pleasure</p>
<p class="tech-p" style="left:635px;top:2698px">Nor again is there anyone who loves or pursues or desires to obtain pain of itself, because it is pain, but because occasionally circumstances occur in which toil</p>
<div class="btn" style="left:635px;top:2825px;width:112px;height:40px">Read More</div>

<section class="shop">
  <h2 class="abs" style="top:82px;left:0;width:1200px;text-align:center;font-family:'Krona One','Arial Black',sans-serif;font-size:36px;color:var(--white)">MY CUSTOM AUTOMOTIVE PARTS</h2>
  <div class="abs" style="left:516px;top:152px;width:168px;height:3px;background:rgba(255,255,255,.8)"></div>
  <p class="abs" style="top:181px;left:0;width:1200px;text-align:center;color:var(--white);font-size:14.5px">I must explain to you how all this mistaken idea of denouncing pleasure and praising pain was born and I will give</p>
  <div class="prod" style="left:111px">
    <div class="ph" role="img" aria-label="Black roller part" style="background:radial-gradient(circle,#5a5a5a 0,#c9c9c9 45%,#fff 70%)"></div>
    <svg class="abs" style="left:197px;top:22px" width="16" height="14" viewBox="0 0 16 14"><path d="M8 13 2 7a3.5 3.5 0 0 1 6-4 3.5 3.5 0 0 1 6 4z" stroke="#f97316" stroke-width="1.5" fill="none"/></svg>
    <div class="btn" style="left:12px;top:222px;width:206px;height:42px;justify-content:space-between;padding:0 22px 0 22px"><span>Shop Now</span><svg width="14" height="12" viewBox="0 0 16 14"><path d="M0 1h3l2 8h9l2-6H4" stroke="#fff" stroke-width="2" fill="none"/><circle cx="6" cy="12" r="1.6" fill="#fff"/><circle cx="13" cy="12" r="1.6" fill="#fff"/></svg></div>
  </div>
  <div class="prod" style="left:361px"><div class="ph" role="img" aria-label="Long black roller shaft" style="background:linear-gradient(135deg,#fff 30%,#3a3a3a 48%,#3a3a3a 52%,#fff 70%)"></div></div>
  <div class="prod" style="left:610px"><div class="ph" role="img" aria-label="Black printer assembly part" style="background:radial-gradient(ellipse,#2a2a2a 0,#6f7780 40%,#fff 72%)"></div></div>
  <div class="prod" style="left:859px"><div class="ph" role="img" aria-label="Yellow and black mechanism part" style="background:radial-gradient(ellipse,#d8c23a 0,#3a3a3a 45%,#fff 72%)"></div></div>
  <div class="prod-meta" style="left:111px"><div class="stars">★★★★☆ &nbsp;( 4 Reviews )</div><div class="pname">Sed ut perspiciatis unde</div><div class="price">$ 20</div></div>
  <div class="prod-meta" style="left:361px"><div class="stars">★★★★☆ &nbsp;( 4 Reviews )</div><div class="pname">Sed ut perspiciatis unde</div><div class="price">$ 20</div></div>
  <div class="prod-meta" style="left:610px"><div class="stars">★★★★☆ &nbsp;( 4 Reviews )</div><div class="pname">Sed ut perspiciatis unde</div><div class="price">$ 20</div></div>
  <div class="prod-meta" style="left:859px"><div class="stars">★★★★☆ &nbsp;( 4 Reviews )</div><div class="pname">Sed ut perspiciatis unde</div><div class="price">$ 20</div></div>
</section>

<h2 class="display abs" style="top:3846px;left:0;width:1200px;text-align:center;font-size:36px">Get A Quote</h2>
<p class="abs" style="top:3940px;left:0;width:1200px;text-align:center;font-size:14.5px;color:#666">We are California's Premiere Speciality Firestopping &amp; Seismic Expansion Joint Contractor</p>
<div class="flabel" style="left:179px;top:4016px">Full Name</div>
<div class="flabel" style="left:617px;top:4016px">Contact Number</div>
<div class="field" style="left:179px;top:4052px;width:405px"><span>John</span><svg width="12" height="12" viewBox="0 0 12 12"><circle cx="6" cy="3.5" r="3" fill="#666"/><path d="M0 12a6 5 0 0 1 12 0z" fill="#666"/></svg></div>
<div class="field" style="left:617px;top:4052px;width:402px"><span>+1 555 014 2290</span><svg width="12" height="12" viewBox="0 0 12 12"><path d="M2 0h3l1 3-2 1a7 7 0 0 0 4 4l1-2 3 1v3c0 1-1 2-2 2A10 10 0 0 1 0 2c0-1 1-2 2-2z" fill="#666"/></svg></div>
<div class="flabel" style="left:179px;top:4133px">Email Address</div>
<div class="flabel" style="left:617px;top:4133px">Upload Files Here</div>
<div class="field" style="left:179px;top:4169px;width:405px"><span>alex.reed@mailbox.example</span><svg width="13" height="10" viewBox="0 0 13 10"><rect width="13" height="10" fill="#666"/><path d="M0 0l6.5 5L13 0" stroke="#edf0f6" fill="none"/></svg></div>
<div class="field" style="left:617px;top:4169px;width:402px"><span>Choose File</span><svg width="14" height="11" viewBox="0 0 14 11"><path d="M3.5 11A3.5 3.5 0 0 1 3 4a4.5 4.5 0 0 1 8.5 1A3 3 0 0 1 11 11z" fill="#666"/><path d="M7 9V5M5 7l2-2 2 2" stroke="#edf0f6" fill="none"/></svg></div>
<div class="flabel" style="left:179px;top:4248px">Comments</div>
<div class="field" style="left:179px;top:4284px;width:840px;height:200px;align-items:flex-start;padding-top:24px"><span>Your Message Goes Here.....</span><svg width="13" height="11" viewBox="0 0 13 11"><path d="M1 0h11v7H5l-3 3V7H1z" fill="#666"/></svg></div>
<div class="btn" style="left:526px;top:4519px;width:146px;height:43px">Submit Here</div>

<footer class="footer">
  <div class="abs" style="left:111px;top:85px;display:flex;align-items:center;gap:12px"><div style="width:30px;height:30px;background:var(--orange)"></div><div style="color:var(--orange);font-weight:700;font-size:22px;line-height:1.25">Kestrel<br>Draft &amp; Design</div></div>
  <div class="fh" style="left:427px">QUICK LINKS</div>
  <div class="fh" style="left:688px">HELP LINKS</div>
  <div class="fh" style="left:929px">FOLLOW US</div>
  <div class="fl" style="left:427px;top:110px">Home<br>About Us<br>Our Services<br>3D Printing Technologies</div>
  <div class="fl" style="left:688px;top:110px">Our Products<br>Testimonials<br>Blogs<br>Contact Us</div>
  <div class="fl" style="left:929px;top:110px">Facebook<br>Instagram<br>Twitter<br>Linkedin</div>
  <div class="abs" style="top:295px;left:0;width:1200px;text-align:center;font-size:14.5px">© 2023 Kestrel Draft &amp; Design | All Rights Reserved.</div>
</footer>
</body>
</html>
```